business card deign

Logo needs the following on it.
1. attached logo
2. Tagline - "From frosty coolers to good times...we've got you covered!"
3. Name- Dalton Pikes, Founder and CPO
4. Address - 412 E. Carver Avenue, Ste 2207, Tampa, FL. 33917
5. Phone - 555.318.4726

```html
<!DOCTYPE html>
<html lang="en">
<head>
<meta charset="utf-8">
<title>Hopley Business Card</title>
<link rel="stylesheet" href="https://fonts.googleapis.com/css2?family=Roboto+Condensed:wght@400;700&family=Arimo:wght@400&display=swap">
<style>
  :root {
    --page-bg: #d2d3d5;
    --card-bg: #151515;
    --ink: #ffffff;
  }
  * { margin: 0; padding: 0; box-sizing: border-box; }
  html, body {
    width: 900px;
    height: 1200px;
    overflow: hidden;
    background: var(--page-bg);
  }
  .canvas {
    position: relative;
    width: 900px;
    height: 1200px;
  }
  .card {
    position: absolute;
    width: 630px;
    height: 357px;
    background: var(--card-bg);
    color: var(--ink);
  }
  .card--front { left: 134px; top: 214px; }
  .card--back  { left: 135px; top: 628px; }

  /* Front */
  .brand-dot {
    position: absolute;
    left: 50%;
    top: 120px;
    width: 56px;
    height: 56px;
    margin-left: -28px;
    border-radius: 50%;
    background: var(--ink);
  }
  .brand-name {
    position: absolute;
    left: 0;
    right: 0;
    top: 234px;
    text-align: center;
    font-family: "Roboto Condensed", sans-serif;
    font-weight: 700;
    font-size: 38px;
    letter-spacing: 15px;
    padding-left: 15px;
    line-height: 1;
  }
  .tagline {
    position: absolute;
    left: 0;
    right: 0;
    top: 302px;
    text-align: center;
    font-family: "Roboto Condensed", sans-serif;
    font-weight: 700;
    font-size: 15.5px;
    letter-spacing: 0.6px;
    line-height: 1;
  }

  /* Back */
  .person {
    position: absolute;
    right: 332px;
    top: 153px;
    text-align: right;
  }
  .person__name {
    font-family: "Roboto Condensed", sans-serif;
    font-weight: 700;
    font-size: 29px;
    line-height: 1;
    letter-spacing: 0.2px;
  }
  .person__title {
    margin-top: 9px;
    font-family: "Arimo", sans-serif;
    font-size: 14.5px;
    line-height: 1;
  }
  .divider {
    position: absolute;
    left: 314px;
    top: 145px;
    width: 1.5px;
    height: 70px;
    background: var(--ink);
  }
  .contact {
    position: absolute;
    left: 333px;
    top: 143px;
    font-family: "Arimo", sans-serif;
  }
  .contact__phone {
    display: flex;
    align-items: center;
    gap: 7px;
    font-size: 16.5px;
    letter-spacing: 1px;
    line-height: 1;
  }
  .contact__phone svg { width: 11px; height: 11px; }
  .contact__address {
    margin-top: 12px;
    margin-left: -2px;
    font-size: 14.5px;
    line-height: 25px;
  }
</style>
</head>
<body>
<div class="canvas">
  <section class="card card--front">
    <div class="brand-dot"></div>
    <div class="brand-name">HOPLEY</div>
    <p class="tagline">From frosty coolers to good times...we've got you covered!</p>
  </section>

  <section class="card card--back">
    <div class="person">
      <div class="person__name">DALTON PIKES</div>
      <div class="person__title">Founder and CPO</div>
    </div>
    <div class="divider"></div>
    <div class="contact">
      <div class="contact__phone">
        <svg viewBox="0 0 24 24" aria-hidden="true"><path fill="#ffffff" d="M6.6 10.8a15.2 15.2 0 0 0 6.6 6.6l2.2-2.2a1 1 0 0 1 1-.25 11.4 11.4 0 0 0 3.6.57 1 1 0 0 1 1 1V20a1 1 0 0 1-1 1A17 17 0 0 1 3 4a1 1 0 0 1 1-1h3.5a1 1 0 0 1 1 1c0 1.25.2 2.45.57 3.570a1 1 0 0 1-.25 1z"/></svg>
        <span>555.318.4726</span>
      </div>
      <div class="contact__address">
        412 E. Carver Avenue, Ste 2207<br>
        Tampa, FL. 33917
      </div>
    </div>
  </section>
</div>
</body>
</html>
```